Brand New Product Needs Sales Focused Website Design

Looking for design of Homepage, Category Page & Product Page for single product sales focused website. TrundleCrate manufacture and distribute a brand new product to the market called PalTote-Case which is a super strong, re-useable, folding & stacking plastic box which can be seen on our current website www.paltote-case.example PalTote-Case was originally developed as an alternative to supermarket carrier bags and was pitched as a box for life against the other low end re-useable products. The original version was made from recycled plastic and pitched very much as environmental product. We are now taking a different direction and have re-designed the boxes in 5 bright and fashionable designs and although we still want the primary focus to be supermarket shopping we want to position the product as a design led, must have shopping and household accessory rather than a boring, cheap looking black plastic box. The new designs will still have the environmental benefits of being able to be re-used thousands of times and being 100% recyclable and save on the imminent 5p tax on carrier bags in the UK however the new designs will not be made from recycled material. Although the main use for PalTote-Case is supermarket shopping it has a multitude of other uses especially where you need temporary storage - laundry, back of the car, moving house/students, gardening, days out, home office filing (will take A4 file), recycling and much more - PalTote-Case is made out of super strong Polypropylene and can be easily washed and sanitised after use and can be folded and unfolded thousands of times and so will last for many years. PalTote-Case is a product that needs to be seen in action to be understood so the web design must quickly and easily communicate what PalTote-Case is and how it works - this can be done with video, images and copy. Our current website does not work for many reasons:- it is too busy, has too much information, tries too hard and ultimately isn't working. Any of the images off our current website can be supplied for use. Once the concept of the website is agreed I can get these photoshopped with the new designs. Pictures of new designs for reference will be attached to this brief. Ultimately we want the website to convert visitors to sales and therefore designers with a proven track record in this field are especially welcome to enter. We also have a Dropbox folder with over 100 product and situation images in - please send email address and we will send an invite to the folder. Due to Christmas period this competition will be run over 15 days however we may choose to extend the deadline to account for the non working days. Any questions feel free to ask - we will respond within 24 hours where possible.

```html
<!DOCTYPE html>
<html lang="en">
<head>
<meta charset="utf-8">
<title>PalTote-Case – Ingenious &amp; Practical</title>
<link href="https://fonts.googleapis.com/css2?family=Open+Sans:wght@400;600;700&display=swap" rel="stylesheet">
<style>
:root{
  --pink:#d9528f;
  --dark:#333337;
  --darker:#2c2c30;
  --text:#555;
  --muted:#aaa;
  --light:#f2f2f2;
  --line:#e4e4e4;
  --footer-link:#8e8e93;
}
*{box-sizing:border-box;margin:0;padding:0}
html,body{width:1103px;height:1200px;overflow:hidden}
body{font-family:"Open Sans",sans-serif;color:var(--text);background:#f3f3f3;position:relative}
a{text-decoration:none;color:inherit}
.wrap{position:absolute;left:101px;width:901px}

/* top bar */
.topbar{position:absolute;top:0;left:0;width:1103px;height:35px;background:#ececec;border-top:2px solid #ddd;border-bottom:1px solid #e0e0e0;font-size:12px;color:#888}
.topbar .welcome{position:absolute;left:101px;top:10px}
.topbar .welcome a{color:var(--pink)}
.topbar .select{position:absolute;top:11px;font-size:11.5px}
.topbar .select::after{content:"";display:inline-block;margin-left:6px;border:3px solid transparent;border-top:4px solid var(--pink);vertical-align:1px}
.topbar .links{position:absolute;right:101px;top:11px;font-size:11.5px;display:flex;gap:12px;color:#999}
.topbar .links .current{color:#333}
.topbar .links svg{width:10px;height:10px;vertical-align:-1px;margin-right:2px}

/* header */
.header{position:absolute;top:35px;left:0;width:1103px;height:99px;background:linear-gradient(#fafafa,#efefef);border-bottom:1px solid #e2e2e2}
.brand{position:absolute;left:101px;top:14px}
.brand .name{font-weight:700;font-size:34px;color:var(--pink);letter-spacing:-0.5px;line-height:1.2}
.brand .tag{font-size:13.5px;color:#222;margin-left:24px;letter-spacing:.3px}
.nav{position:absolute;left:441px;top:34px;height:43px;display:flex;background:var(--dark);border-radius:3px;overflow:hidden}
.nav a{display:flex;align-items:center;justify-content:center;color:#bbb;font-size:13.5px;border-right:1px solid #444}
.nav a:last-child{border-right:0}
.nav a.active{background:var(--pink);color:#fff}

/* slider */
.slider{top:156px;height:352px;background:#fff;box-shadow:0 2px 4px rgba(0,0,0,.25);border-radius:2px;overflow:hidden}
.slide-photo{position:absolute;left:360px;top:3px;right:3px;height:310px;background:radial-gradient(ellipse at 55% 55%,#f4f4f4 0,#d8d8d8 60%,#a9a9a9 100%)}
.slide-photo .box{position:absolute;left:90px;top:75px;width:370px;height:200px;border-radius:6px;background:linear-gradient(180deg,#fafafa 0,#f1eef2 70%,#a9c844 70%,#9bbd3c 100%);transform:skewY(-6deg)}
.slide-panel{position:absolute;left:3px;top:3px;width:480px;height:310px}
.slide-panel svg{position:absolute;inset:0}
.slide-copy{position:absolute;left:21px;top:18px;color:#fff}
.slide-copy .name{font-weight:700;font-size:44px;letter-spacing:-1px;line-height:1.2}
.slide-copy .lead{font-size:21px;margin-top:12px}
.slide-copy .sub{font-size:20.5px;line-height:33px;margin-top:6px}
.thumbs{position:absolute;left:21px;top:236px;display:flex;gap:11px}
.thumbs span{width:62px;height:62px;border-radius:50%;border:4px solid #fff;background:radial-gradient(circle,#8a4a23 0,#6b3617 55%,#f4f4f4 56%)}
.price{position:absolute;left:241px;top:236px;color:#fff;font-weight:600}
.price .cur{font-size:26px;vertical-align:16px}
.price .big{font-size:54px;line-height:1}
.price .cents{font-size:30px}
.price .was{display:block;font-size:14px;color:#6b2444;text-decoration:line-through;font-weight:400;margin-top:2px}
.dots{position:absolute;left:21px;top:330px;display:flex;gap:3px}
.dots i{width:9px;height:9px;border-radius:50%;background:#d6d6d6}
.dots i:first-child{background:#777}

/* category cards */
.cards{top:533px;height:148px;display:flex;gap:5px}
.card{flex:1;background:linear-gradient(#fff,#ececec);border:1px solid #e3e3e3}
.card h3{height:37px;background:var(--dark);color:#fff;font-weight:600;font-size:15.5px;text-align:center;line-height:37px}
.card.active h3{background:var(--pink)}
.card .shot{width:156px;height:80px;margin:14px auto 0;border-radius:4px}
.shot.floral{background:linear-gradient(180deg,#f7f3f6 0,#f1e4ec 70%,#a6c543 70%)}
.shot.geo{background:linear-gradient(180deg,#f8f8f8 0,#eeeeee 62%,#c58a66 62%,#e8c1b0 100%)}

/* features */
.features{top:708px;height:220px;display:flex}
.feature{flex:1;text-align:center;border-left:1px solid var(--line);border-right:1px solid var(--line);margin-right:-1px;padding-top:33px}
.feature .icon{width:62px;height:62px;margin:0 auto;border:2px solid var(--pink);border-radius:50%;display:flex;align-items:center;justify-content:center}
.feature .icon svg{width:34px;height:34px}
.feature h4{font-weight:400;font-size:20px;color:#333;margin-top:13px}
.feature p{font-size:12px;line-height:16.5px;color:#aaa;margin:8px auto 0;width:190px}
.feature .more{display:block;font-size:10px;color:#555;margin-top:10px}

/* footer */
.footer{position:absolute;top:958px;left:0;width:1103px;height:242px;background:var(--dark)}
.fcol{position:absolute;top:29px}
.fcol h5{font-weight:400;font-size:14.5px;color:#fff;margin-bottom:4px}
.fcol a,.fcol p{display:block;font-size:12.5px;color:var(--footer-link);line-height:20px}
.newsletter{left:772px;width:230px}
.signup{display:flex;margin-top:10px;height:30px}
.signup span{flex:1;background:#f0f0f0;font-size:10px;font-style:italic;color:#888;padding:9px 10px}
.signup b{background:var(--pink);color:#fff;font-weight:400;font-size:13px;padding:6px 8px}
.follow{color:#fff;font-size:14.5px;margin-top:14px}
.social{display:flex;gap:7px;margin-top:10px}
.social i{width:22px;height:22px;border-radius:50%;background:#eee}
.copyright{position:absolute;left:0;bottom:0;width:1103px;height:40px;border-top:1px solid #3e3e42;text-align:center;font-size:12.5px;color:var(--footer-link);line-height:42px}
</style>
</head>
<body>

<div class="topbar">
  <div class="welcome">Welcome to Brightwell HD, <a href="#">Login</a> or <a href="#">Create new account</a></div>
  <div class="select" style="left:497px">US DOLLER</div>
  <div class="select" style="left:590px">ENGLISH</div>
  <div class="links">
    <a class="current" href="#"><svg viewBox="0 0 10 10"><path d="M5 1 0 5.5h1.5V9h2.5V6.5h2V9h2.5V5.5H10z" fill="#333"/></svg>Home</a>
    <a href="#"><svg viewBox="0 0 10 10"><circle cx="5" cy="3" r="2.3" fill="#aaa"/><path d="M1 10c0-3 2-4.5 4-4.5S9 7 9 10z" fill="#aaa"/></svg>My Account</a>
    <a href="#"><svg viewBox="0 0 10 10"><path d="M0 1h2l1.5 5h5L10 2.5H3" fill="none" stroke="#aaa" stroke-width="1.2"/><circle cx="4" cy="8.5" r="1" fill="#aaa"/><circle cx="8" cy="8.5" r="1" fill="#aaa"/></svg>Shopping Cart</a>
    <a href="#"><svg viewBox="0 0 10 10"><circle cx="5" cy="5" r="4.2" fill="none" stroke="#aaa"/><path d="M3 5l1.5 1.5L7.2 3.6" fill="none" stroke="#aaa"/></svg>CheckOut</a>
  </div>
</div>

<header class="header">
  <div class="brand">
    <div class="name">PalTote-Case</div>
    <div class="tag">INGENENIOUS &amp; PRACTICAL</div>
  </div>
  <nav class="nav">
    <a class="active" href="#" style="width:80px">Home</a>
    <a href="#" style="width:100px">About Us</a>
    <a href="#" style="width:161px">Shop Our Products</a>
    <a href="#" style="width:108px">Need Help</a>
    <a href="#" style="width:112px">Contact Us</a>
  </nav>
</header>

<section class="wrap slider">
  <div class="slide-photo" role="img" aria-label="Product photo of an open floral-print folding box with green base band">
    <div class="box"></div>
  </div>
  <div class="slide-panel">
    <svg viewBox="0 0 480 310" preserveAspectRatio="none"><polygon points="0,0 480,0 360,310 0,310" fill="var(--pink)"/></svg>
    <div class="slide-copy">
      <div class="name">PalTote-Case</div>
      <div class="lead">Ingenenious &amp; Practical Box For Life</div>
      <div class="sub">NOW Available In 5 BRIGHT and<br>FASHIONABLE designs</div>
    </div>
    <div class="thumbs">
      <span role="img" aria-label="Brown leather satchel"></span>
      <span role="img" aria-label="Brown leather folio"></span>
      <span role="img" aria-label="Wooden crate"></span>
    </div>
    <div class="price"><span class="cur">$</span><span class="big">99</span><span class="cents">.89</span><span class="was">$109.99</span></div>
  </div>
  <div class="dots"><i></i><i></i><i></i><i></i><i></i></div>
</section>

<section class="wrap cards">
  <div class="card active"><h3>Lorem Ipsum Dolor Sit</h3><div class="shot floral" role="img" aria-label="Floral design box"></div></div>
  <div class="card"><h3>Amet Consectutuer</h3><div class="shot geo" role="img" aria-label="Geometric pattern box"></div></div>
  <div class="card"><h3>Adipicsing Diam Set</h3><div class="shot floral" role="img" aria-label="Floral design box"></div></div>
  <div class="card"><h3>Nonummy Elite</h3><div class="shot geo" role="img" aria-label="Geometric pattern box"></div></div>
</section>

<section class="wrap features">
  <div class="feature">
    <div class="icon"><svg viewBox="0 0 34 34"><text x="17" y="29" text-anchor="middle" font-family="Open Sans,sans-serif" font-weight="700" font-size="30" fill="var(--pink)">?</text></svg></div>
    <h4>About Us</h4>
    <p>Lorem ipsum dolor sit amet, consectetur adipiscing elit, Sed do euismod tempor magna aliqua.</p>
    <a class="more" href="#">+ READ MORE</a>
  </div>
  <div class="feature">
    <div class="icon"><svg viewBox="0 0 34 34" fill="none" stroke="var(--pink)" stroke-width="1.8"><path d="M5 14h24l-3 13H8z"/><path d="M11 14l6-7 6 7"/><path d="M13 18v5M17 18v5M21 18v5"/></svg></div>
    <h4>Shop Our Products</h4>
    <p>Lorem ipsum dolor sit amet, consectetur adipiscing elit, Sed do euismod tempor magna aliqua.</p>
    <a class="more" href="#">+ READ MORE</a>
  </div>
  <div class="feature">
    <div class="icon"><svg viewBox="0 0 34 34" fill="none" stroke="var(--pink)" stroke-width="2"><circle cx="17" cy="17" r="5"/><path d="M17 4v4M17 26v4M4 17h4M26 17h4M7.8 7.8l2.8 2.8M23.4 23.4l2.8 2.8M7.8 26.2l2.8-2.8M23.4 10.6l2.8-2.8"/><circle cx="17" cy="17" r="10"/></svg></div>
    <h4>Need Help?</h4>
    <p>Lorem ipsum dolor sit amet, consectetur adipiscing elit, Sed do euismod tempor magna aliqua.</p>
    <a class="more" href="#">+ READ MORE</a>
  </div>
  <div class="feature">
    <div class="icon"><svg viewBox="0 0 34 34"><path d="M9 14a8 8 0 0 1 16 0" fill="none" stroke="var(--pink)" stroke-width="1.8"/><rect x="7" y="13" width="4" height="6" rx="1" fill="var(--pink)"/><rect x="23" y="13" width="4" height="6" rx="1" fill="var(--pink)"/><path d="M6 31c1-6 5-8 11-8s10 2 11 8z" fill="var(--pink)"/></svg></div>
    <h4>Call PalTote Case</h4>
    <p>Lorem ipsum dolor sit amet, consectetur adipiscing elit, Sed do euismod tempor magna aliqua.</p>
    <a class="more" href="#">+ READ MORE</a>
  </div>
</section>

<footer class="footer">
  <div class="fcol" style="left:101px"><h5>Site Links</h5><a href="#">Home</a><a href="#">About Us</a><a href="#">Shop Our Products</a><a href="#">Need Help</a></div>
  <div class="fcol" style="left:265px"><h5>About PalTote Case</h5><a href="#">Our Mission</a><a href="#">Blog</a><a href="#">Why Choose Us</a></div>
  <div class="fcol" style="left:436px"><h5>Our Boxes</h5><a href="#">Watch A Live Demo</a><a href="#">View Our Products</a><a href="#">Smartphone Apps</a></div>
  <div class="fcol" style="left:604px"><h5>Having Trouble?</h5><a href="#">Knowledge Base</a><a href="#">Discussion Forum</a><a href="#">Contact Us</a></div>
  <div class="fcol newsletter"><h5>Our Newsletter</h5><p>Subscribe To Our E-mail List for Sales &amp; Updates.</p>
    <div class="signup"><span>Email..</span><b>Subscribe</b></div>
    <div class="follow">Follow Us On :</div>
    <div class="social"><i></i><i></i><i></i><i></i></div>
  </div>
  <div class="copyright">Copyrights 2014 PalTote Case - All Rights Reserved</div>
</footer>

</body>
</html>
```